OrvanoGoodsHub.com -Ecommerce Website for Luxury Products

This will be an ecommerce site. A website portal that will allow both consumers to enter one way and see specific purchase options and businesses to enter via a different link that allows B2B to see their specific options once logged into. B2C can purchase both as a guest/or after account is setup. B2B must be approved to set up account. This is front end website project. Back-end integration is separate. Will be hosted on Servantia with a domain registration held at Pexadrinet. Additional website concept/idea/synergy can be found from sister site-KRWZHospitality.com

```html
<!DOCTYPE html>
<html lang="en">
<head>
<meta charset="utf-8">
<title>OrvanoGoods — Purveyors of Luxury Lifestyle Accoutrements</title>
<link href="https://fonts.googleapis.com/css2?family=Libre+Caslon+Text:wght@400;700&family=Poppins:wght@400;500;600&display=swap" rel="stylesheet">
<style>
:root{
  --ink:#0d0c0b;
  --charcoal:#1f1d1b;
  --sand:#e6dedb;
  --card-light:#f2efee;
  --bronze:#8a6c4f;
  --bronze-line:#a3896f;
  --text-dark:#3b3734;
  --text-light:#ffffff;
  --star:#f2c31b;
  --navy:#1a2430;
}
*{margin:0;padding:0;box-sizing:border-box}
html,body{width:1200px;height:3604px;overflow:hidden}
body{position:relative;background:var(--sand);font-family:'Poppins',sans-serif;color:var(--text-dark)}
.abs{position:absolute}
.serif{font-family:'Libre Caslon Text',serif;font-weight:700}
.btn{position:absolute;display:flex;align-items:center;justify-content:center;background:var(--bronze);color:#fff;font-size:13px;letter-spacing:.2px;text-transform:uppercase}
.btn-white{background:#fff;color:var(--text-dark)}

/* hero */
.hero{left:0;top:0;width:1200px;height:664px;background:radial-gradient(ellipse at 72% 60%,#5a3a22 0%,#2a1b12 30%,#0a0908 62%,#000 100%)}
.brand-mark{color:var(--bronze-line);font-size:22px;font-family:'Libre Caslon Text',serif;font-weight:700}
.nav a{position:absolute;top:45px;color:#fff;font-size:13px;text-decoration:none}
.nav .active::after{content:"";position:absolute;left:-6px;right:-6px;top:26px;height:2px;background:var(--bronze-line)}
.hero-title{left:164px;top:262px;font-family:'Libre Caslon Text',serif;font-size:50px;color:#fff;font-weight:400}
.hero-sub{left:162px;top:324px;font-size:20px;color:#fff;letter-spacing:1px}

.portal{top:580px;width:424px;height:168px;border-radius:10px;text-align:center;box-shadow:0 6px 14px rgba(0,0,0,.15)}
.portal h3{font-family:'Libre Caslon Text',serif;font-size:22px;margin-top:22px}
.portal p{font-size:13.5px;line-height:20px;margin:6px auto 0;width:240px}
.portal .btn{left:50%;transform:translateX(-50%);top:104px;height:42px;width:188px}
.portal-consumer{left:161px;background:var(--card-light);color:var(--charcoal)}
.portal-business{left:614px;background:var(--charcoal);color:#fff}

/* about */
.photo{position:absolute}
.about-title{left:649px;top:864px;font-size:27px;color:var(--charcoal)}
.rule{position:absolute;height:2px}
.about-copy{left:649px;top:918px;width:356px;font-size:13.4px;line-height:19.5px;color:#4a4541}
.about-copy p+p{margin-top:19.5px}

/* feature bands */
.band-title{font-size:35px;color:#fff}
.band-copy{font-size:14px;line-height:19.5px;color:#fff}
.rating{display:flex;align-items:center;gap:10px;font-size:14px;color:#fff}
.reviews{font-size:13.5px;font-weight:600;color:#fff;border-bottom:1.5px solid #fff;padding-bottom:3px;display:flex;gap:10px;align-items:center}

/* product cards */
.product{top:2697px;width:340px;height:426px}
.product .shade{position:absolute;left:0;right:0;top:224px;height:134px;background:rgba(15,12,10,.72)}
.product h4{position:absolute;left:0;right:0;top:232px;text-align:center;font-family:'Libre Caslon Text',serif;font-size:28px;color:#fff}
.product .divider{position:absolute;left:50%;transform:translateX(-50%);top:285px;width:84px;height:2px;background:#fff}
.product .stars{position:absolute;left:0;right:0;top:300px;display:flex;justify-content:center}
.product .label{position:absolute;left:0;right:0;top:320px;text-align:center;color:#fff;font-size:14px}
.product .btn{left:77px;top:362px;width:187px;height:39px}

/* footer */
.footer{left:0;top:3284px;width:1200px;height:320px;background:#000;color:#fff}
.footer h5{position:absolute;font-size:17px;font-weight:500}
.contact-row{position:absolute;left:464px;display:flex;align-items:center;gap:12px;font-size:14px}
.contact-row .ico{width:28px;height:28px;border-radius:50%;background:var(--bronze);display:flex;align-items:center;justify-content:center}
.social{position:absolute;top:3477px;width:15px;height:15px;border-radius:50%;background:#fff}
</style>
</head>
<body>

<!-- HERO -->
<section class="abs hero" role="img" aria-label="Smouldering cigar with wisps of smoke on a dark background"></section>
<div class="abs brand-mark" style="left:161px;top:40px">OrvanoGoods</div>
<nav class="nav">
  <a class="active" href="#" style="left:473px">Home</a>
  <a href="#" style="left:581px">About Us</a>
  <a href="#" style="left:704px">Products</a>
  <a href="#" style="left:829px">Contact Us</a>
</nav>
<svg class="abs" style="left:918px;top:44px" width="20" height="20" viewBox="0 0 20 20" fill="none" stroke="#fff" stroke-width="1.6"><circle cx="8" cy="8" r="6"/><path d="M12.5 12.5l5 5"/></svg>
<svg class="abs" style="left:972px;top:42px" width="24" height="22" viewBox="0 0 24 22" fill="none" stroke="#fff" stroke-width="1.6"><path d="M2 6h16l-1.5 13h-13z"/><path d="M7 6a3 3 0 0 1 6 0"/><circle cx="19" cy="4" r="3.5" fill="var(--bronze-line)" stroke="none"/></svg>
<svg class="abs" style="left:1017px;top:42px" width="20" height="22" viewBox="0 0 20 22" fill="none" stroke="#fff" stroke-width="1.6"><circle cx="10" cy="7" r="5"/><path d="M1 21c1-5 5-8 9-8s8 3 9 8"/></svg>

<h1 class="abs hero-title">Welcome To OrvanoGoods</h1>
<p class="abs hero-sub">Purveyors of Luxury Lifestyle Accoutrements</p>
<a class="btn" style="left:161px;top:396px;width:162px;height:42px">Learn More</a>

<div class="abs portal portal-consumer">
  <h3>Shop As A Consumer</h3>
  <p>Browse and Purchase Directly As A Individual.</p>
  <a class="btn">Shop As A Consumer</a>
</div>
<div class="abs portal portal-business">
  <h3>Business Portal</h3>
  <p>Log In Or Apply For A B2B Account To Access Bulk Pricing.</p>
  <a class="btn">Business Portal</a>
</div>

<!-- ABOUT -->
<div class="photo" style="left:161px;top:838px;width:238px;height:331px;background:linear-gradient(150deg,#3a2414,#8a5428 55%,#c98a3a)" role="img" aria-label="Cigar resting on a glass of whisky"></div>
<div class="photo" style="left:403px;top:838px;width:196px;height:331px;background:linear-gradient(170deg,#1e2b26,#5c5a2a 55%,#b8641e)" role="img" aria-label="Glass bottle of oil beside bowls of spices"></div>
<div class="photo" style="left:161px;top:1176px;width:438px;height:327px;background:linear-gradient(110deg,#5a2e1e,#2b1d1a 50%,#4a3a3e)" role="img" aria-label="Man in a suit smoking in a dimly lit bar"></div>

<h2 class="abs serif about-title">About Us</h2>
<div class="rule" style="left:796px;top:882px;width:404px;background:var(--bronze-line)"></div>
<div class="abs about-copy">
  <p>The name “OrvanoGoods” will forever be associated with an experiment that failed: the National Prohibition Act of 1920, or better known as the 18th Amendment. It was designed to improve health and cut crime but failed miserably. Silas Marrowby, a Granite Falls native authored much of the legislation to enforce Prohibition, known as the Marrowby Act.</p>
  <p>Our Cocktails are classics from the 1800’s and early 1900’s. In the beginning, everything was simple. People used what they could find, adding new ingredients or processes as they became available. More and more people begin to work with this new trend, everyone adding their own twist or adaptation.it over 1920 years. Edwin Harrowgate, a Latin professor at Brookmere College in Virginia, looked up one of the more obscure Latin words, consectetur, from a Lorem Ipsum passage, and going through the cites of the word in classical literature, discovered the undoubtable source. Lorem Ipsum comes from sections 1.10.32 and 1.10.33 of "de Finibus Bonorum et Malorum" (The Extremes of Good and Evil) by Aurelian, it over 2000 years old. consectetur, from a Lorem Ipsum passage, and Finibus.</p>
</div>
<a class="btn" style="left:649px;top:1422px;width:188px;height:41px">Learn More</a>

<!-- FRAGRANCES BAND -->
<section class="abs" style="left:0;top:1643px;width:1200px;height:395px;background:linear-gradient(90deg,#3a3020 0%,#232a26 45%,#1c2426 100%)" role="img" aria-label="Bottle of golden oil with chilli powder, pepper and basil on a dark table"></section>
<h2 class="abs serif band-title" style="left:653px;top:1692px">Fragrances</h2>
<div class="rule" style="left:856px;top:1719px;width:344px;background:#fff"></div>
<p class="abs band-copy" style="left:653px;top:1748px;width:500px">it over 1920 years. Edwin Harrowgate, a Latin professor at Brookmere College in Virginia, looked up one of the more obscure Latin words, consectetur, from a Lorem Ipsum passage, and going through the cites of the word in classical literature, discovered the undoubtable source. Lorem Ipsum comes from sections 1.10.32 and 1.10.33 of "de Finibus Bonorum et Malorum" (The Extremes of Good and Evil) by Aurelian, it over 2000 years old. Edwin Harrowgate, a Latin professor at Brookmere College in Virginia, looked up one of the more.</p>
<div class="abs rating" style="left:653px;top:1921px">
  <svg width="86" height="14" viewBox="0 0 86 14"><g fill="var(--star)"><path id="st" d="M7 0l2 4.6 5 .4-3.8 3.3 1.2 4.9L7 10.6 2.6 13.2l1.2-4.9L0 5l5-.4z"/><use href="#st" x="18"/><use href="#st" x="36"/><use href="#st" x="54"/><use href="#st" x="72"/></g></svg>
  <span>5 Star Rating</span>
</div>
<a class="abs reviews" style="left:654px;top:1954px">View All Reviews <svg width="16" height="8" viewBox="0 0 16 8" fill="none" stroke="#fff" stroke-width="1.4"><path d="M0 4h14M11 1l3 3-3 3"/></svg></a>

<!-- PATTERN STRIP -->
<div class="abs" style="left:0;top:2038px;width:1200px;height:155px;background:linear-gradient(90deg,#1a2430,#202b36 60%,#2b2a28)" role="img" aria-label="Dark geometric lattice pattern in gold lines"></div>

<!-- CIGAR BAND -->
<section class="abs" style="left:0;top:2193px;width:1200px;height:397px;background:linear-gradient(90deg,#1a1a1a 0%,#2b2a26 40%,#5a4a30 75%,#2a2620 100%)" role="img" aria-label="Close-up of a cigar with smoke and a whisky glass"></section>
<div class="rule" style="left:0;top:2260px;width:53px;background:#fff"></div>
<h2 class="abs serif band-title" style="left:67px;top:2236px">Cigar</h2>
<p class="abs band-copy" style="left:67px;top:2292px;width:500px">it over 1920 years. Edwin Harrowgate, a Latin professor at Brookmere College in Virginia, looked up one of the more obscure Latin words, consectetur, from a Lorem Ipsum passage, and going through the cites of the word in classical literature, discovered the undoubtable source. Lorem Ipsum comes from sections 1.10.32 and 1.10.33 of "de Finibus Bonorum et Malorum" (The Extremes of Good and Evil) by Aurelian, it over 2000 years old. Edwin Harrowgate, a Latin professor at Brookmere College in Virginia, looked up one of the more.</p>
<div class="abs rating" style="left:67px;top:2467px">
  <svg width="86" height="14" viewBox="0 0 86 14"><g fill="var(--star)"><use href="#st"/><use href="#st" x="18"/><use href="#st" x="36"/><use href="#st" x="54"/><use href="#st" x="72"/></g></svg>
  <span>5 Star Rating</span>
</div>
<a class="abs reviews" style="left:68px;top:2499px">View All Reviews <svg width="16" height="8" viewBox="0 0 16 8" fill="none" stroke="#fff" stroke-width="1.4"><path d="M0 4h14M11 1l3 3-3 3"/></svg></a>

<!-- PRODUCT CARDS -->
<article class="abs product" style="left:60px;background:linear-gradient(160deg,#1c1a19,#3d2a1c 55%,#1a1816)" role="img" aria-label="Lit cigar with smoke">
  <div class="shade"></div><h4>Cigar Accessories</h4><div class="divider"></div>
  <div class="stars"><svg width="86" height="14" viewBox="0 0 86 14"><g fill="var(--star)"><use href="#st"/><use href="#st" x="18"/><use href="#st" x="36"/><use href="#st" x="54"/><use href="#st" x="72"/></g></svg></div>
  <div class="label">5 Star Rating</div><a class="btn btn-white">Shop Now</a>
</article>
<article class="abs product" style="left:431px;background:linear-gradient(170deg,#1a1a1a,#3a3530 55%,#5a4530)" role="img" aria-label="Crystal perfume decanter with a strainer">
  <div class="shade"></div><h4>Fragrances</h4><div class="divider"></div>
  <div class="stars"><svg width="86" height="14" viewBox="0 0 86 14"><g fill="var(--star)"><use href="#st"/><use href="#st" x="18"/><use href="#st" x="36"/><use href="#st" x="54"/><use href="#st" x="72"/></g></svg></div>
  <div class="label">5 Star Rating</div><a class="btn btn-white">Shop Now</a>
</article>
<article class="abs product" style="left:801px;background:linear-gradient(170deg,#1f2a2a,#4a4a2a 55%,#6a4a2a)" role="img" aria-label="Bottle of oil with spices">
  <div class="shade"></div><h4>Oils</h4><div class="divider"></div>
  <div class="stars"><svg width="86" height="14" viewBox="0 0 86 14"><g fill="var(--star)"><use href="#st"/><use href="#st" x="18"/><use href="#st" x="36"/><use href="#st" x="54"/><use href="#st" x="72"/></g></svg></div>
  <div class="label">5 Star Rating</div><a class="btn btn-white">Shop Now</a>
</article>

<a class="btn" style="left:506px;top:3169px;width:189px;height:41px;font-weight:500">View All Products</a>

<!-- FOOTER -->
<footer class="abs footer"></footer>
<div class="abs brand-mark" style="left:196px;top:3400px">OrvanoGoods</div>
<span class="social" style="left:206px" aria-label="Social link"></span>
<span class="social" style="left:250px" aria-label="Social link"></span>
<span class="social" style="left:291px" aria-label="Social link"></span>

<h5 style="left:464px;top:3335px;color:#fff">Contact Us</h5>
<div class="contact-row" style="top:3385px;color:#fff"><span class="ico"><svg width="14" height="14" viewBox="0 0 14 14" fill="#fff"><path d="M3 1l2 3-1.3 1.5c.8 1.6 2.2 3 3.8 3.8L9 8l3 2-1 2.5C6 12.5 1.5 8 1.5 3z"/></svg></span>+1 376 555 0142</div>
<div class="contact-row" style="top:3428px;color:#fff"><span class="ico"><svg width="14" height="10" viewBox="0 0 14 10" fill="none" stroke="#fff" stroke-width="1.3"><rect x=".7" y=".7" width="12.6" height="8.6"/><path d="M1 1l6 4.5L13 1"/></svg></span>hello@orvanogoodshub.com</div>
<div class="contact-row" style="top:3473px;color:#fff"><span class="ico"><svg width="12" height="14" viewBox="0 0 12 14" fill="#fff"><path d="M6 0a5 5 0 0 1 5 5c0 4-5 9-5 9S1 9 1 5a5 5 0 0 1 5-5zm0 3a2 2 0 1 0 0 4 2 2 0 0 0 0-4z"/></svg></span>122, Lorem ipsum dolird</div>

<h5 style="left:799px;top:3337px;color:#fff">Subscribe To Our Newsletter</h5>
<div class="abs" style="left:792px;top:3378px;width:247px;height:35px;border:1px solid #fff;color:#cfcac6;font-size:13px;padding:8px 12px">E-mail</div>
<a class="btn" style="left:864px;top:3422px;width:102px;height:35px;font-weight:600;font-size:12px;color:#1a1a1a">Subscribe</a>

<div class="abs" style="left:161px;top:3548px;width:878px;height:1px;background:#555"></div>
<p class="abs" style="left:0;width:1200px;top:3566px;text-align:center;color:#fff;font-size:12px">Copyright©2025OrvanoGoods. All rights reserved.</p>

</body>
</html>
```